School Communication Email Template

Looking for a designer to create a couple simple email templates that are matching our brand colors and feel. Attached is the default email template that is currently being sent out. Company details can be shared upon request.

Template is to be used within the booking tool we use (snapshot below) and gmail. Template code is in HTML (see screenshot below).
Updates

Template code for website should be in HTML. Sorry if that created confusion.

Target Market(s)

Parents of kids enrolled in our classes

Industry/Entity Type

Kids sport classes

Font styles to use
Serif

Colors
0054AA
0677BA
7BADD7
CADEEF
E8F1F8
FFF300
FFF600
FEFA6F
FFFEC7
FFFEE8

Requirements
Must have
• Consistency with company brand/colors
Nice to have
• Flexibility to be adjusted as needed

```html
<!DOCTYPE html>
<html lang="en">
<head>
<meta charset="utf-8">
<title>Booking Confirmation</title>
<link rel="stylesheet" href="https://fonts.googleapis.com/css2?family=Work+Sans:wght@400;500;600;700&family=Mulish:wght@400;500&display=swap">
<style>
  :root {
    --page-bg: #e4e4e4;
    --accent-yellow: #fbbd2c;
    --brand-navy: #243f8a;
    --card-bg: #ffffff;
    --label-ink: #2b2b2b;
    --muted-ink: #444444;
  }
  * { box-sizing: border-box; margin: 0; padding: 0; }
  html, body {
    width: 1027px;
    height: 1200px;
    overflow: hidden;
  }
  body {
    position: relative;
    background: var(--page-bg);
    font-family: "Work Sans", sans-serif;
  }
  .top-band {
    position: absolute; left: 0; top: 0;
    width: 100%; height: 9px;
    background: var(--accent-yellow);
  }
  .bottom-band {
    position: absolute; left: 0; bottom: 0;
    width: 100%; height: 11px;
    background: var(--brand-navy);
  }
  .brand {
    position: absolute; left: 0; top: 114px;
    width: 100%;
    display: flex; justify-content: center; align-items: center;
    gap: 14px;
  }
  .brand-dot {
    width: 30px; height: 30px; border-radius: 50%;
    background: var(--accent-yellow);
  }
  .brand-name {
    font-family: "Work Sans", sans-serif;
    font-weight: 700;
    font-size: 34px;
    color: var(--brand-navy);
  }
  .booking-card {
    position: absolute;
    left: 62px; top: 267px;
    width: 909px; height: 818px;
    background: var(--card-bg);
    box-shadow: 0 0 18px rgba(0,0,0,0.06);
  }
  .greeting {
    position: absolute; left: 0; top: 0;
    width: 288px; height: 60px;
    background: var(--brand-navy);
    color: #ffffff;
    font-size: 23px; font-weight: 500;
    padding-left: 34px;
    display: flex; align-items: center;
  }
  .card-title {
    position: absolute; right: 46px; top: 33px;
    font-size: 29px; font-weight: 700;
    color: var(--brand-navy);
  }
  .booking-form {
    position: absolute; left: 0; top: 112px; width: 100%;
  }
  .form-row {
    display: flex; align-items: center;
    height: 62px; margin-bottom: 37px;
  }
  .field-label {
    width: 245px; padding-left: 52px;
    font-size: 20px; font-weight: 400;
    color: var(--label-ink);
    letter-spacing: 0.4px;
  }
  .field-group { display: flex; gap: 22px; }
  .field {
    width: 615px; height: 62px;
    border: 1.3px solid var(--brand-navy);
    display: flex; align-items: center; justify-content: space-between;
    padding: 0 20px 0 22px;
    font-family: "Mulish", sans-serif;
    font-size: 19px;
    color: var(--brand-navy);
  }
  .field-half { width: 296px; }
  .field-icon { width: 28px; height: 28px; }
  .copyright {
    position: absolute; left: 0; top: 1131px;
    width: 100%; text-align: center;
    font-family: "Mulish", sans-serif;
    font-size: 15px; color: var(--muted-ink);
  }
</style>
</head>
<body>
  <div class="top-band"></div>

  <header class="brand">
    <span class="brand-dot"></span>
    <span class="brand-name">Starling Sports</span>
  </header>

  <main class="booking-card">
    <div class="greeting">Dear Daniel Carver</div>
    <h1 class="card-title">Booking</h1>

    <div class="booking-form">
      <div class="form-row">
        <span class="field-label">Student</span>
        <div class="field-group">
          <div class="field field-half">Lucy</div>
          <div class="field field-half">Carver</div>
        </div>
      </div>

      <div class="form-row">
        <span class="field-label">Appointment</span>
        <div class="field">Request For Swimming</div>
      </div>

      <div class="form-row">
        <span class="field-label">Service</span>
        <div class="field">Swimming</div>
      </div>

      <div class="form-row">
        <span class="field-label">Start Date</span>
        <div class="field">18/02/2023
          <svg class="field-icon" viewBox="0 0 24 24" fill="none" stroke="currentColor" stroke-width="1.4">
            <rect x="3" y="4.5" width="18" height="16.5" rx="2"/>
            <line x1="3" y1="9" x2="21" y2="9"/>
            <line x1="8" y1="2.5" x2="8" y2="6"/>
            <line x1="16" y1="2.5" x2="16" y2="6"/>
            <g fill="currentColor" stroke="none">
              <circle cx="7.5" cy="12.5" r="0.9"/><circle cx="10.5" cy="12.5" r="0.9"/><circle cx="13.5" cy="12.5" r="0.9"/><circle cx="16.5" cy="12.5" r="0.9"/>
              <circle cx="7.5" cy="15.5" r="0.9"/><circle cx="10.5" cy="15.5" r="0.9"/><circle cx="13.5" cy="15.5" r="0.9"/><circle cx="16.5" cy="15.5" r="0.9"/>
              <circle cx="7.5" cy="18.3" r="0.9"/><circle cx="10.5" cy="18.3" r="0.9"/><circle cx="13.5" cy="18.3" r="0.9"/>
            </g>
          </svg>
        </div>
      </div>

      <div class="form-row">
        <span class="field-label">End Date</span>
        <div class="field">20/02/2023
          <svg class="field-icon" viewBox="0 0 24 24" fill="none" stroke="currentColor" stroke-width="1.4">
            <rect x="3" y="4.5" width="18" height="16.5" rx="2"/>
            <line x1="3" y1="9" x2="21" y2="9"/>
            <line x1="8" y1="2.5" x2="8" y2="6"/>
            <line x1="16" y1="2.5" x2="16" y2="6"/>
            <g fill="currentColor" stroke="none">
              <circle cx="7.5" cy="12.5" r="0.9"/><circle cx="10.5" cy="12.5" r="0.9"/><circle cx="13.5" cy="12.5" r="0.9"/><circle cx="16.5" cy="12.5" r="0.9"/>
              <circle cx="7.5" cy="15.5" r="0.9"/><circle cx="10.5" cy="15.5" r="0.9"/><circle cx="13.5" cy="15.5" r="0.9"/><circle cx="16.5" cy="15.5" r="0.9"/>
              <circle cx="7.5" cy="18.3" r="0.9"/><circle cx="10.5" cy="18.3" r="0.9"/><circle cx="13.5" cy="18.3" r="0.9"/>
            </g>
          </svg>
        </div>
      </div>

      <div class="form-row">
        <span class="field-label">Start Time</span>
        <div class="field">10.:00 AM
          <svg class="field-icon" viewBox="0 0 24 24" fill="none" stroke="currentColor" stroke-width="1.6">
            <circle cx="12" cy="12" r="9.5"/>
            <polyline points="12,6.5 12,12 15.5,14.5"/>
          </svg>
        </div>
      </div>

      <div class="form-row">
        <span class="field-label">End TIme</span>
        <div class="field">04.:00 PM
          <svg class="field-icon" viewBox="0 0 24 24" fill="none" stroke="currentColor" stroke-width="1.6">
            <circle cx="12" cy="12" r="9.5"/>
            <polyline points="12,6.5 12,12 15.5,14.5"/>
          </svg>
        </div>
      </div>
    </div>
  </main>

  <footer class="copyright">Copyright © 2023 All Rights Reserved</footer>

  <div class="bottom-band"></div>
</body>
</html>
```